New Fun, Positive, energised looking Business Card Needed for High Achiever Coach

I am looking for a two sided full colour business card. I am self employed and have recently re branded my 1-2-1 work re-vitalising high achievers. My target client base for these cards is therefore high achievers - usually aged 40 -55, they are often entrepreneurs, CEO or work in banking and finance and 2/3 are male. I work with them on 90 day or 6 month coaching programs to help them live their success in a healthier, more sustainable and fulfiiled way. They pay for this privately so though they are corporate types the cards need not look 'corporate'. I want to portray the idea of transformation, vitality and re-connecting.
You can get a feel for the look I like on my new website: morvenlisk.co.uk
I want to use this logo with strapline (Re-Vitalising High Achievers) (I purchased off Logoharbor) and font/ colours (the turquoise and green).
Details to include on the card:
www.morvenlisk.co.uk
+44 7915 302618
morven@morvenlisk.co.uk
skype: morvenlisk
I'd also like to include:
Do you struggle to switch off? Want to be healthier and feel fitter? Want closer relationships? More clarity over the direction you are headed? I can help you do these things using integrated mind-body techniques. Visit morvenlisk.co.uk TODAY to apply for a FREE Breakthrough session.
BUT if that is too much text for a card I am open to advice/ammendments.
Updates
Thanks for your design - I am considering them. PLease change the wording to :

```html
<!DOCTYPE html>
<html lang="en">
<head>
<meta charset="utf-8">
<title>Morven Lisk – Business Card</title>
<link rel="stylesheet" href="https://fonts.googleapis.com/css2?family=Open+Sans:wght@400;600;700&display=swap">
<style>
  :root {
    --page: #e9e6e1;
    --silver-light: #f4f5f6;
    --silver-mid: #dcdfe2;
    --silver-dark: #c4c8cc;
    --turquoise: #1ba3cf;
    --green: #5cb84a;
    --white: #ffffff;
    --ink: #3a3d40;
    --strap: #4f93b5;
  }
  * { box-sizing: border-box; margin: 0; padding: 0; }
  html, body {
    width: 1200px; height: 720px; overflow: hidden;
    background: var(--page);
    font-family: "Open Sans", Arial, sans-serif;
  }
  .sheet { position: relative; width: 1200px; height: 720px; }
  .card {
    position: absolute; top: 202px;
    width: 540px; height: 315px;
    background: linear-gradient(135deg, var(--silver-light) 0%, var(--silver-mid) 45%, var(--silver-light) 70%, var(--silver-dark) 100%);
    box-shadow: 0 6px 18px rgba(0,0,0,0.15);
    overflow: hidden;
  }
  .card--front { left: 40px; }
  .card--back { left: 620px; }

  .front-waves { position: absolute; inset: 0; width: 100%; height: 100%; }

  .brand { position: absolute; left: 34px; top: 120px; }
  .brand__row { display: flex; align-items: center; gap: 10px; }
  .brand__dot { width: 30px; height: 30px; border-radius: 50%; background: var(--green); flex: none; }
  .brand__name { font-weight: 700; font-size: 30px; color: var(--turquoise); letter-spacing: 0.5px; white-space: nowrap; }
  .brand__strap { margin-top: 4px; margin-left: 40px; font-size: 13px; color: var(--strap); white-space: nowrap; }

  .contacts {
    position: absolute; left: 350px; top: 112px;
    list-style: none; color: var(--white);
    font-size: 12px; line-height: 22px;
  }
  .contacts li { display: flex; align-items: center; gap: 7px; white-space: nowrap; }
  .contact__icon { width: 13px; height: 13px; flex: none; display: block; }
  .contact__mark { width: 12px; height: 12px; border-radius: 50%; background: var(--white); flex: none; margin: 0 0.5px; }

  .pitch {
    position: absolute; inset: 0;
    display: flex; flex-direction: column; justify-content: center; align-items: center;
    text-align: center; color: var(--ink);
    font-size: 16.5px; line-height: 22px;
    padding: 0 30px;
  }
  .pitch p + p { margin-top: 10px; }
  .pitch strong { font-weight: 700; }
</style>
</head>
<body>
<main class="sheet">

  <section class="card card--front" aria-label="Card front">
    <svg class="front-waves" viewBox="0 0 540 315" preserveAspectRatio="none" aria-hidden="true">
      <path d="M0,282 C140,272 220,232 265,175 C305,122 380,86 540,78 L540,315 L0,315 Z" fill="var(--turquoise)"/>
      <path d="M0,274 C140,264 215,224 260,167 C300,114 378,78 540,70" fill="none" stroke="var(--green)" stroke-width="5"/>
      <path d="M0,266 C138,256 210,216 255,160 C295,106 375,70 540,62" fill="none" stroke="var(--white)" stroke-width="4"/>
      <path d="M0,303 C140,302 250,286 320,248" fill="none" stroke="var(--white)" stroke-width="3"/>
      <path d="M0,296 C140,294 245,278 312,242" fill="none" stroke="var(--green)" stroke-width="3"/>
    </svg>

    <div class="brand">
      <div class="brand__row">
        <span class="brand__dot"></span>
        <span class="brand__name">Morven Lisk</span>
      </div>
      <div class="brand__strap">Re-Vitalising High Achievers</div>
    </div>

    <ul class="contacts">
      <li>
        <svg class="contact__icon" viewBox="0 0 16 16"><circle cx="8" cy="8" r="7" fill="none" stroke="#fff" stroke-width="1.4"/><path d="M5.5 4.5l1.5 0 .6 2-1 .8a5 5 0 0 0 2.2 2.2l.8-1 2 .6v1.5c-3.5.3-6.4-2.6-6.1-6.1z" fill="#fff"/></svg>
        <span>+44 7915 302618</span>
      </li>
      <li>
        <svg class="contact__icon" viewBox="0 0 16 16"><rect x="1.5" y="3.5" width="13" height="9" rx="1" fill="none" stroke="#fff" stroke-width="1.4"/><path d="M2 4l6 5 6-5" fill="none" stroke="#fff" stroke-width="1.4"/></svg>
        <span>morven@morvenlisk.co.uk</span>
      </li>
      <li>
        <svg class="contact__icon" viewBox="0 0 16 16"><circle cx="8" cy="8" r="6.5" fill="none" stroke="#fff" stroke-width="1.3"/><ellipse cx="8" cy="8" rx="3" ry="6.5" fill="none" stroke="#fff" stroke-width="1.1"/><path d="M1.5 8h13" stroke="#fff" stroke-width="1.1"/></svg>
        <span>www.morvenlisk.co.uk</span>
      </li>
      <li>
        <span class="contact__mark"></span>
        <span>morvenlisk</span>
      </li>
    </ul>
  </section>

  <section class="card card--back" aria-label="Card back">
    <div class="pitch">
      <p>Do you struggle to switch off?<br>
      Want to be healthier and feel fitter?<br>
      Want closer relationships?<br>
      More clarity over the direction you are headed?</p>
      <p>I can help you do these things using integrated<br>
      mind-body techniques.</p>
      <p>Visit <strong>morvenlisk.co.uk</strong> TODAY to apply for a<br>
      FREE Breakthrough session.</p>
    </div>
  </section>

</main>
</body>
</html>
```